New Webpage for High Class Expert Witness Services Company

We are looking for a minimalist design for a webpage that just has our logo and an entry form offer to connect with one of our Liaisons.
The entry form should just ask for Name, Email, Contact Info and Description of Project.

Company Name is: The Marlowe Crest Advisory Services

Number of Pages Required

1 page

```html
<!DOCTYPE html>
<html lang="en">
<head>
<meta charset="utf-8">
<title>The Marlowe Crest Advisory Services — Connect with a Liaison</title>
<link rel="stylesheet" href="https://fonts.googleapis.com/css2?family=Source+Serif+4:wght@400;500&family=Poppins:wght@400;500&display=swap">
<style>
  :root {
    --bg-deep: #0f1520;
    --bg-mid: #1b2433;
    --ink: #e9ecf1;
    --ink-soft: #c9ced8;
    --placeholder: #6c7382;
    --field: #151a26;
    --line: rgba(233, 236, 241, 0.75);
    --card: rgba(20, 26, 38, 0.45);
  }
  * { box-sizing: border-box; margin: 0; padding: 0; }
  html, body { width: 1200px; height: 800px; overflow: hidden; }
  body { position: relative; background: var(--bg-deep); color: var(--ink); font-family: "Source Serif 4", Georgia, serif; }

  .backdrop {
    position: absolute; inset: 0;
    background:
      radial-gradient(ellipse 380px 520px at 95% 45%, rgba(60,72,92,.55), transparent 70%),
      radial-gradient(ellipse 420px 600px at 10% 40%, rgba(52,62,80,.6), transparent 70%),
      radial-gradient(ellipse 500px 160px at 20% 95%, rgba(90,100,118,.35), transparent 70%),
      linear-gradient(180deg, var(--bg-mid) 0%, var(--bg-deep) 60%, #121824 100%);
  }

  .brand { position: absolute; left: 36px; top: 50px; display: flex; align-items: center; gap: 12px; }
  .brand-mark { width: 16px; height: 16px; background: var(--ink-soft); }
  .brand-name { font-family: "Source Serif 4", Georgia, serif; font-weight: 500; font-size: 18px; letter-spacing: 1.2px; text-transform: uppercase; color: var(--ink-soft); line-height: 1; }

  .intro { position: absolute; left: 100px; width: 345px; top: 222px; text-align: center; }
  .intro-the { font-size: 24px; letter-spacing: 1px; }
  .intro-name { font-size: 38px; letter-spacing: 5px; margin-top: 4px; color: #d9dde4; }
  .intro-sub { font-size: 14px; letter-spacing: 1.2px; margin-top: 6px; color: var(--ink-soft); word-spacing: 2px; }
  .divider { display: block; margin: 30px auto 0; }
  .intro-tagline { font-size: 19.5px; line-height: 23px; margin-top: 38px; }

  .liaison-card {
    position: absolute; left: 573px; top: 78px; width: 475px; height: 627px;
    border: 1px solid var(--line); border-radius: 22px; background: var(--card);
  }
  .card-title { position: absolute; top: 34px; width: 100%; text-align: center; font-size: 28px; letter-spacing: 2.4px; font-weight: 400; color: #dfe2e8; }
  .card-sub { position: absolute; top: 69px; width: 100%; text-align: center; font-size: 14px; letter-spacing: 1px; word-spacing: 3px; }

  .field-label { position: absolute; left: 56px; font-family: "Poppins", Arial, sans-serif; font-size: 11.5px; font-weight: 500; }
  .field {
    position: absolute; left: 51px; width: 374px; height: 39px;
    background: var(--field); border: 1px solid var(--line); border-radius: 4px;
    font-family: "Poppins", Arial, sans-serif; font-size: 11.5px; color: var(--placeholder);
    padding: 0 11px; display: flex; align-items: center;
  }
  .field-area { height: 114px; align-items: flex-start; padding-top: 12px; }
  .country-code { width: 61px; gap: 5px; padding: 0 5px; }
  .phone-number { left: 118px; width: 307px; }
  .submit {
    position: absolute; left: 51px; top: 540px; width: 374px; height: 50px;
    border: 1px solid var(--line); border-radius: 4px; background: var(--field);
    font-family: "Poppins", Arial, sans-serif; font-size: 18px; font-weight: 500; color: var(--ink);
    display: flex; align-items: center; justify-content: center;
  }

  .footer { position: absolute; top: 758px; width: 100%; text-align: center; font-size: 14px; letter-spacing: 1px; color: var(--ink-soft); padding-left: 70px; }
  .footer .dot { margin: 0 8px; }
</style>
</head>
<body>
  <div class="backdrop" role="img" aria-label="Dim courthouse scene with stone columns and steps on the left and a statue of Lady Justice holding scales on the right"></div>

  <header class="brand">
    <span class="brand-mark"></span>
    <span class="brand-name">Marlowe Crest Advisory Services</span>
  </header>

  <section class="intro">
    <div class="intro-the">The</div>
    <div class="intro-name">Marlowe Crest</div>
    <div class="intro-sub">Advisory Service &nbsp;&nbsp;.&nbsp;&nbsp; Expert Witness Liaison</div>
    <svg class="divider" width="322" height="14" viewBox="0 0 322 14">
      <line x1="0" y1="7" x2="145" y2="7" stroke="#c9ced8" stroke-width="1"/>
      <rect x="155" y="3" width="8" height="8" transform="rotate(45 159 7)" fill="none" stroke="#c9ced8" stroke-width="1"/>
      <line x1="177" y1="7" x2="322" y2="7" stroke="#c9ced8" stroke-width="1"/>
    </svg>
    <p class="intro-tagline">Get connected with top experts—<br>speak to a Liaison today.</p>
  </section>

  <form class="liaison-card">
    <h1 class="card-title">Connect with a Liaison</h1>
    <p class="card-sub">Confidential &nbsp;&nbsp;.&nbsp;&nbsp; No Obligation</p>

    <label class="field-label" style="top:129px">Full NAME*</label>
    <div class="field" style="top:150px">Evan Holloway</div>

    <label class="field-label" style="top:208px">E-mail*</label>
    <div class="field" style="top:229px">evan.holloway@mailbox.test</div>

    <label class="field-label" style="top:287px">Phone Number</label>
    <div class="field country-code" style="top:310px">
      <svg width="14" height="10" viewBox="0 0 14 10">
        <rect width="14" height="10" fill="#b8343d"/>
        <rect y="1.4" width="14" height="1.4" fill="#fff"/>
        <rect y="4.2" width="14" height="1.4" fill="#fff"/>
        <rect y="7" width="14" height="1.4" fill="#fff"/>
        <rect width="6" height="5.4" fill="#3c3b6e"/>
      </svg>
      <span>+1</span>
      <svg width="8" height="5" viewBox="0 0 8 5"><path d="M1 1l3 3 3-3" fill="none" stroke="#6c7382" stroke-width="1"/></svg>
    </div>
    <div class="field phone-number" style="top:310px">5550142378</div>

    <label class="field-label" style="top:368px">Description of project</label>
    <div class="field field-area" style="top:392px">Write Description of the project here ....</div>

    <div class="submit">Submit</div>
  </form>

  <footer class="footer">© 2026<span class="dot">·</span>The Marlowe Crest Advisory Services<span class="dot">·</span>All Rights Reserved</footer>
</body>
</html>
```